Brightway Haus Inc. Business Card Design

Brightway Haus Inc. is in search of a great clean design for our business cards!

Looking to incorporate our full logo and watermark on side one (however, I am open to having the text and watermark separated within the design.)

On side two, I am looking to have contact information (Name, Position, Phone #, Email, Website (www.thebrightwayhaus.ca). Can have the logo and/or watermark as part of the design if applicable.

Please add tagline "Where Shine Counts" on either side 1 or 2. This tagline can be in a sans serif, serif or cursive font as long as it compliments overall design. Capitalization can be title or sentence case depending on how it fits within the design.

Get creative!! Looking for a clean, crisp, premium design! Looking for a glossy card finish with spot UV features when printed. Cards will also be printed with rounded corners. Standard dimensions (3.5 x 2).

Target Market(s)

B2B - primary clients are business owners or property management corporations. (residential jobs are few and far between)

Industry/Entity Type

Business

Contact Information for Business Card

- clean, crisp design
- double sided
- spot UV accents and glossy finish upon printing
- standard business card size (3.5 x 2) with rounded corners
- please see project description for requirements per side

Font styles to use
Sans Serif

Requirements
Must have
• - adequate bleeds with print ready files
• - cohesive design elements between side 1 & 2
• - spot UV elements (can be on both sides or just one, use your discretion)
• - colour pallet should match the logo file provided
• - incorporate tagline "where shine counts" (this tagline can be in a serif or sans serif font as long as it is complimentary to the overall design.
Nice to have
• - Premium elements with a clean design
Should not have
• - Please omit cartoon or whimsical like designs, think premium.
• - Colours should not stray from the pallet of the provided logo.

```html
<!DOCTYPE html>
<html lang="en">
<head>
<meta charset="utf-8">
<title>Brightway Haus Inc. Business Card</title>
<link href="https://fonts.googleapis.com/css2?family=Roboto+Condensed:ital,wght@0,400;0,700;1,400&family=Roboto:wght@400;500&display=swap" rel="stylesheet">
<style>
  :root {
    --teal: #12b3b5;
    --navy: #1c2452;
    --ink: #4a4a4a;
    --paper: #f4f4f4;
    --backdrop: #2b2b2b;
    --white: #ffffff;
  }
  * { box-sizing: border-box; margin: 0; padding: 0; }
  html, body { width: 1200px; height: 960px; overflow: hidden; }
  body { background: var(--backdrop); position: relative; font-family: "Roboto", sans-serif; }

  .card { position: absolute; width: 600px; height: 342px; border-radius: 22px; overflow: hidden; }
  .card--front { left: 314px; top: 113px; background: var(--paper); }
  .card--back { left: 311px; top: 472px; background: var(--teal); }

  .brand-name {
    position: absolute; left: 0; right: 0; top: 68px; text-align: center;
    font-family: "Roboto Condensed", sans-serif; font-weight: 700; font-size: 44px;
    color: var(--teal); letter-spacing: 0.5px;
  }

  .identity { position: absolute; right: 320px; top: 166px; text-align: right; }
  .identity__name { font-family: "Roboto Condensed", sans-serif; font-weight: 700; font-size: 22px; color: var(--teal); line-height: 24px; }
  .identity__role { font-family: "Roboto Condensed", sans-serif; font-weight: 700; font-size: 16px; color: var(--navy); line-height: 19px; }
  .identity__line { font-size: 14px; color: var(--ink); line-height: 19px; }

  .divider { position: absolute; left: 300px; top: 166px; width: 1px; height: 80px; background: #9a9a9a; }

  .contacts { position: absolute; left: 322px; top: 170px; list-style: none; }
  .contacts li { display: flex; align-items: center; height: 19px; font-size: 14px; color: var(--ink); }
  .contacts svg { width: 14px; height: 14px; margin-right: 9px; fill: var(--teal); flex: none; }

  .wave { position: absolute; left: 0; top: 0; width: 600px; height: 342px; }
  .website {
    position: absolute; left: 0; right: 0; top: 316px; text-align: center;
    font-size: 14px; letter-spacing: 5px; color: var(--white);
  }

  .back-mark {
    position: absolute; left: 0; right: 0; top: 128px; display: flex; justify-content: center; align-items: center; gap: 14px;
    font-family: "Roboto Condensed", sans-serif; font-weight: 700; font-size: 46px; color: var(--white);
  }
  .back-mark__square { width: 30px; height: 30px; background: var(--white); }

  .tagline {
    position: absolute; left: 0; right: 0; top: 280px; display: flex; justify-content: center; align-items: center; gap: 6px;
    font-family: "Roboto Condensed", sans-serif; font-style: italic; font-size: 20px; color: var(--white);
  }
  .tagline__rule { width: 100px; height: 1px; background: linear-gradient(90deg, rgba(255,255,255,0), var(--white)); }
  .tagline__rule--right { background: linear-gradient(90deg, var(--white), rgba(255,255,255,0)); }
</style>
</head>
<body>

<section class="card card--front">
  <div class="brand-name">Brightway Haus Inc.</div>

  <div class="identity">
    <div class="identity__name">MARA ELLISON</div>
    <div class="identity__role">CEO/FOUNDER</div>
    <div class="identity__line">120 Harbour Row</div>
    <div class="identity__line">Vancouver, BC V6B 1A1</div>
  </div>

  <div class="divider"></div>

  <ul class="contacts">
    <li><svg viewBox="0 0 24 24"><path d="M6.6 10.8a15.2 15.2 0 0 0 6.6 6.6l2.2-2.2c.3-.3.7-.4 1-.2 1.1.4 2.3.6 3.6.6.6 0 1 .4 1 1V20c0 .6-.4 1-1 1A17 17 0 0 1 3 4c0-.6.4-1 1-1h3.5c.6 0 1 .4 1 1 0 1.3.2 2.5.6 3.6.1.3 0 .7-.2 1z"/></svg>604 555 0182</li>
    <li><svg viewBox="0 0 24 24"><path d="M7 1h10a2 2 0 0 1 2 2v18a2 2 0 0 1-2 2H7a2 2 0 0 1-2-2V3a2 2 0 0 1 2-2zm0 3v14h10V4zm5 15.5a1 1 0 1 0 0 2 1 1 0 0 0 0-2z"/></svg>604 555 0147</li>
    <li><svg viewBox="0 0 24 24"><path d="M6 2h12v5H6zM3 8h18a2 2 0 0 1 2 2v7h-4v5H5v-5H1v-7a2 2 0 0 1 2-2zm4 8v4h10v-4z"/></svg>604 555 0199</li>
    <li><svg viewBox="0 0 24 24"><path d="M2 5h20v14H2zm2 2v.4l8 5 8-5V7zm0 2.8V17h16V9.8l-8 5z"/></svg>hello@brightwayhaus.ca</li>
  </ul>

  <svg class="wave" viewBox="0 0 600 342" aria-hidden="true">
    <path d="M0 312 C150 292 300 318 450 296 C520 286 570 272 600 262 L600 342 L0 342 Z" fill="var(--teal)"/>
    <path d="M4 304 C120 278 260 282 400 284 C480 285 550 272 600 258 L600 264 C550 282 480 296 400 298 C260 300 130 294 4 310 Z" fill="var(--navy)"/>
  </svg>
  <div class="website">www.thebrightwayhaus.ca</div>
</section>

<section class="card card--back">
  <div class="back-mark"><span class="back-mark__square"></span><span>Brightway Haus Inc.</span></div>
  <div class="tagline">
    <span class="tagline__rule"></span>
    <span>Where Shine Counts</span>
    <span class="tagline__rule tagline__rule--right"></span>
  </div>
</section>

</body>
</html>
```